Cyber Security firm working in the Financial Services sector needs a brochure

We need a brochure covering our products and offerings. We work exclusively with Independent Broker Dealers, their Reps and RIAs in the US. We help them keep their computers secure and compliant with applicable regulations and policies. Have attached samples of our logo an descriptions of our products and services.

Target Market(s)

Financial Institutions and Financial Advisors

Industry/Entity Type

Financial Service

```html
<!DOCTYPE html>
<html lang="en">
<head>
<meta charset="utf-8">
<title>Ledgerwall Cyber – Services Brochure</title>
<link rel="stylesheet" href="https://fonts.googleapis.com/css2?family=Open+Sans:wght@400;600;700;800&display=swap">
<style>
  :root {
    --navy: #1b3f8f;
    --blue: #1f6fc4;
    --sky: #2aa3e0;
    --ink: #3a4350;
    --body-bg: #e6eaee;
    --column-bg: #cfd8e0;
    --page-bg: #ffffff;
    --canvas-bg: #eeeeee;
  }
  * { box-sizing: border-box; margin: 0; padding: 0; }
  html, body { width: 1200px; height: 960px; overflow: hidden; background: var(--canvas-bg); }
  body { font-family: "Open Sans", Arial, sans-serif; color: var(--ink); }

  .brochure {
    position: absolute; left: 250px; top: 24px;
    width: 700px; height: 912px;
    background: var(--page-bg);
    box-shadow: 0 6px 24px rgba(0,0,0,.15);
    overflow: hidden;
  }
  .main-column {
    position: absolute; left: 0; top: 0; width: 430px; height: 812px;
    background: var(--body-bg);
  }
  .side-column {
    position: absolute; left: 430px; top: 0; width: 270px; height: 812px;
    background: var(--column-bg);
    padding: 26px 22px 0 22px;
  }
  .header-band {
    position: absolute; left: 0; top: 0; width: 430px; height: 200px;
  }
  .header-text {
    position: absolute; left: 26px; top: 52px; width: 380px; color: #fff;
  }
  .header-text h2 { color: #fff; font-size: 15px; font-weight: 800; text-transform: uppercase; letter-spacing: .2px; }
  .header-text p { font-size: 8.5px; line-height: 1.45; margin: 3px 0 12px; }

  .main-body { position: absolute; left: 26px; top: 218px; width: 384px; }
  h3 { font-size: 12.5px; font-weight: 700; color: #1d2430; margin: 10px 0 4px; }
  ul.check-list { list-style: disc; padding-left: 22px; font-size: 8.4px; line-height: 1.5; }

  .section-title {
    color: var(--navy); font-size: 15px; font-weight: 800; text-transform: uppercase;
    line-height: 1.1; margin: 14px 0 6px;
  }
  .side-column .section-title { margin-top: 16px; }
  .side-column .section-title:first-child { margin-top: 0; }
  p.copy { font-size: 8.4px; line-height: 1.5; text-align: justify; margin-bottom: 6px; }

  .brand {
    position: absolute; left: 450px; top: 748px; display: flex; align-items: center; gap: 8px;
  }
  .brand-dot { width: 16px; height: 16px; border-radius: 50%; background: var(--navy); }
  .brand-name { font-size: 15px; font-weight: 800; color: var(--navy); }

  .contact-bar {
    position: absolute; left: 22px; top: 832px; width: 700px; height: 56px;
    border: 2px solid var(--navy); border-right: none; border-radius: 28px 0 0 28px;
    display: flex; align-items: center; padding-left: 30px;
    font-size: 11px; font-weight: 700; color: #1d2430; gap: 14px;
  }
  .contact-bar .divider { width: 1px; height: 14px; background: #1d2430; }
</style>
</head>
<body>
<article class="brochure">
  <section class="main-column">
    <svg class="header-band" viewBox="0 0 430 200" preserveAspectRatio="none" aria-hidden="true">
      <defs>
        <linearGradient id="bandGradient" x1="0" y1="0" x2="1" y2="0">
          <stop offset="0" stop-color="#1b3f8f"/>
          <stop offset="1" stop-color="#2aa3e0"/>
        </linearGradient>
      </defs>
      <polygon points="0,40 400,0 430,0 430,200 0,200" fill="url(#bandGradient)"/>
    </svg>
    <div class="header-text">
      <h2>New Computer Sourcing</h2>
      <p>We are an authorized Northbay Systems Value Added Reseller and will be happy to help you get your new computer. We work with you to determine an appropriate configuration and what would be a good fit for your specific needs.</p>
      <h2>New Computer Configuration</h2>
      <p>Configuration services provided for new computers. These can be sourced from us or locally and shipped to us or done remotely. Price $300.</p>
    </div>

    <div class="main-body">
      <h3>Configure for Broker Dealer security requirements</h3>
      <ul class="check-list">
        <li>Encrypt the Drive</li>
        <li>Set password Policy</li>
        <li>Set Screen saver timeout policy</li>
        <li>Apply all Operating System patches</li>
        <li>Set computer for Auto-update of all products where possible (if not subscribing to our Managed Software Patching service)</li>
        <li>Install default Anti-Virus software and configure to policy requirements (if not subscribing to our Managed Anti-Virus service)</li>
      </ul>
      <h3>Configure for functionality</h3>
      <ul class="check-list">
        <li>Remove any unneeded software</li>
        <li>Configure browsers to function most reliably with BD sites</li>
        <li>Remove any unneeded Browser Plug-ins or Tool Bars</li>
        <li>Install Kettle Runtime (as required)</li>
        <li>Install Pagely Reader</li>
        <li>Install Quillsoft Office if needed – We can provide Office for $199</li>
      </ul>
      <h3>Safety</h3>
      <ul class="check-list">
        <li>Create a System Image to an external encrypted drive</li>
        <li>Create Encryption Recovery media and keys if applicable</li>
      </ul>

      <h2 class="section-title">General Computer Support</h2>
      <p class="copy">Ledgerwall Cyber has a long history of working with thousands of Independent Financial Advisors and Broker Dealers across the country. Because of this we have a lot of experience in supporting their technology needs. A benefit of this is we not only understand the technology but also the special needs of the financial services industry. All our technicians are US based, have years of industry experience and must pass a rigorous background check. We also understand your security requirements and will execute appropriate non-disclosure agreements to help you insure your information remains private. We've found we can resolve most software and configuration issues remotely. Our rates are $95 per hour.</p>

      <h2 class="section-title">Internet Blocking and Filtering</h2>
      <p class="copy">Comprehensive security for your network through award-winning phishing, botnet and malware site protection. Our web filtering service delivers network security services through the DNS layer blocking known malicious or infected sites from resolving on your network. This also allows you to block specific web sites and also broad categories of content from being accessed from your locations. A couple of examples might be Gambling and Pornography. $3.50 per month per device.</p>
    </div>
  </section>

  <aside class="side-column">
    <h2 class="section-title">Security Awareness Training</h2>
    <p class="copy">Security Awareness Training is a critical component of a comprehensive cyber security program. Because the cyber security environment is continuously changing, it is our experience that a multi-level approach is most effective in providing timely, actionable information as well as a firm grasp of critical security principles and requirements.</p>
    <p class="copy">Our first level is a targeted, electronic delivery of mini training modules, typically taking no longer than 10 minutes to complete, every 4-6 weeks. These short, topical modules are designed to highlight current attacks and the appropriate response to the illustrated threat. The attacks are explained in an easy-to-understand format with the amount of technical jargon kept to the bare minimum. Each module presents several multiple choice questions to insure the respondent has a firm grasp of the topic. The continuous "drip" nature of this timely information is important in keeping security top-of-mind.</p>
    <p class="copy">Our second level provides periodic phishing emails. The emails consist of both general phishing emails, spear phishing, as well as very targeted "whaling" types of email. Anyone found susceptible to opening specially crafted attachments or links will be immediately taken to an on-line refresher course on how to spot fraudulent emails. $25 per user per year.</p>

    <h2 class="section-title">Firewall Sales</h2>
    <p class="copy">We provide pre-purchase consulting, configuration and support for business grade firewalls. We will help you spec an appropriate firewall, determine if VPN access is needed as well as any dedicated guest Wireless Access. The most suitable device for your location as well as any satellite locations is dependent on organization size and complexity. Prices starting at $750.</p>

    <h2 class="section-title">Public IP Monitoring</h2>
    <p class="copy">Knowing what the world sees of your front door to the internet is important. Our Public IP Monitoring scans your static IP address daily looking for inappropriate ports being made available over the Internet. If we find your device has changes made we contact you to verify the changes were intentional and explain the ramifications of the changes. We don't want your network exposed because the Tech installing your new copier decided to open up a number of ports on your firewall. $100 per year per IP address.</p>
  </aside>

  <div class="brand">
    <span class="brand-dot" aria-hidden="true"></span>
    <span class="brand-name">Ledgerwall Cyber</span>
  </div>

  <footer class="contact-bar">
    <span>Phone: 555-010-2841</span>
    <span class="divider"></span>
    <span>Email: info@ledgerwallcyber.com</span>
    <span>www.ledgerwallcyber.com</span>
  </footer>
</article>
</body>
</html>
```